Maplecrest Disability - Social Security Disability Attorneys

Our company is expanding to attract clients nationwide for our social security disability practice. We have a logo, but I am looking for a creative and elegant letterhead that projects an image of being technologically advanced but still professional enough for the legal field. I am looking for the "wow factor" combined with this is still professional enough for a law practice.

Requesting letterhead and business card design
Updates

Had to update and change the logo. The previous logo had a typo. Please send updates with the new logo for consideration. The letterhead and business cards should be professional enough to be used for a law firm. Thanks.

Industry/Entity Type

Law Practice, Law Firm, Healthcare Industry, Government

Colors

Designer to choose colors to be used in the design.

Requirements
Nice to have
• **Please create a vertical design for the business card**

```html
<!DOCTYPE html>
<html lang="en">
<head>
<meta charset="utf-8">
<title>Maplecrest Disability – Letterhead</title>
<link rel="stylesheet" href="https://fonts.googleapis.com/css2?family=Poppins:wght@400;500&display=swap">
<style>
  :root {
    --backdrop: #e4e4e6;
    --paper: #ffffff;
    --brand-blue: #4a74e8;
    --brand-orange: #f57f26;
    --ink: #1f1f1f;
    --muted: #6b6b6b;
  }
  * { box-sizing: border-box; margin: 0; padding: 0; }
  html, body {
    width: 1200px; height: 960px; overflow: hidden;
    background: var(--backdrop);
  }
  .letterhead {
    position: absolute; left: 270px; top: 30px;
    width: 660px; height: 900px;
    background: var(--paper);
    box-shadow: 0 6px 24px rgba(0,0,0,0.12);
    overflow: hidden;
    font-family: "Poppins", sans-serif;
  }
  .brand {
    position: absolute; left: 64px; top: 150px;
    display: flex; align-items: center; gap: 10px;
  }
  .brand-mark {
    width: 12px; height: 12px;
    background: var(--brand-orange);
    flex: none;
  }
  .brand-name {
    font-weight: 500; font-size: 20px;
    color: var(--ink);
    line-height: 1.1;
  }
  .brand-tagline {
    position: absolute; left: 86px; top: 178px;
    font-size: 9.5px; color: var(--muted);
  }
  .contact {
    position: absolute; left: 405px; top: 52px;
    padding-left: 18px;
    border-left: 1.5px solid var(--brand-orange);
    font-size: 10.5px; font-style: normal;
    color: var(--ink); line-height: 1.55;
  }
  .contact-address { margin-bottom: 2px; }
  .contact-line { display: flex; align-items: center; gap: 7px; }
  .contact-icon { width: 10px; height: 10px; flex: none; }
  .footer-rule {
    position: absolute; left: 0; bottom: 34px;
    width: 100%; height: 4px;
    background: var(--brand-orange);
  }
  .footer-band {
    position: absolute; left: 0; bottom: 0;
    width: 100%; height: 26px;
    background: var(--brand-blue);
  }
</style>
</head>
<body>
  <main class="letterhead">
    <header class="brand">
      <span class="brand-mark"></span>
      <span class="brand-name">Maplecrest Disability</span>
    </header>
    <p class="brand-tagline">Social Security Disability Attorneys</p>

    <address class="contact">
      <div class="contact-address">Suite 4, level 12, Harbour Lane<br>Sydney NSW 2000</div>
      <div class="contact-line">
        <svg class="contact-icon" viewBox="0 0 10 10" aria-hidden="true"><path d="M2 1 L4 1 L4.6 3 L3.5 4 C4 5.3 4.8 6 6 6.5 L7 5.4 L9 6 L9 8 C9 8.6 8.6 9 8 9 C4.4 9 1 5.6 1 2 C1 1.4 1.4 1 2 1Z" fill="var(--brand-orange)"/></svg>
        <span>555-210-4873</span>
      </div>
      <div class="contact-line">
        <svg class="contact-icon" viewBox="0 0 10 10" aria-hidden="true"><rect x="0.5" y="2" width="9" height="6.5" rx="0.8" fill="var(--brand-orange)"/><path d="M0.8 2.4 L5 5.6 L9.2 2.4" stroke="#fff" stroke-width="0.9" fill="none"/></svg>
        <span>info@maplecrestdisability.com</span>
      </div>
      <div class="contact-line">
        <svg class="contact-icon" viewBox="0 0 10 10" aria-hidden="true"><circle cx="5" cy="5" r="4.5" fill="var(--brand-orange)"/><path d="M0.5 5 H9.5 M5 0.5 C3 3 3 7 5 9.5 M5 0.5 C7 3 7 7 5 9.5" stroke="#fff" stroke-width="0.7" fill="none"/></svg>
        <span>www.maplecrestdisability.com</span>
      </div>
    </address>

    <div class="footer-rule"></div>
    <div class="footer-band"></div>
  </main>
</body>
</html>
```